Design a large parking banner – mandatory ticket validation in the shop

Banner Size:
548 cm (width) x 154 cm (height)
Note: The banner will be placed in a metal frame at our parking lot entrance, fully visible to every incoming truck driver. The message must be easy to read from a distance.
Goal of the Banner:
To inform all truck drivers that they must validate their entry ticket inside the shop, even if they are parking for a short time.
The message must be displayed in multiple languages for international drivers.
Mandatory Content:
Main message – in multiple languages (clearly separated or stacked):
Dutch (NL): Vergeet je ticket niet te valideren in de shop – verplicht, ook bij kort parkeren!
French (FR): N'oubliez pas de valider votre ticket à la boutique – obligatoire, même pour un court arrêt !
English (EN): Don't forget to validate your entry ticket in the shop – mandatory, even for short stops!
German (DE): Vergessen Sie nicht, Ihr Einfahrticket im Shop zu entwerten – Pflicht, auch bei kurzem Parken!
Polish (PL): Nie zapomnij zatwierdzić biletu w sklepie – obowiązkowe, nawet przy krótkim postoju!
Romanian (RO): Nu uitați să validați biletul în magazin – obligatoriu, chiar și pentru opriri scurte!
You can include more languages if space allows, but these are essential.
Opening Hours Block (in one section below):
Shop Opening Hours
Mon – Fri: 05:30 – 22:00
Sat & Sun: 08:00 – 22:00
Style & Branding:
The design must match the visual identity of Haulport 41Ter
Please refer to the attached photos of existing parking signage for guidance on colors, typography, and layout style
Our logo (attached) must be clearly visible and professionally integrated
Feel free to use icons or pictograms to visually support the message (e.g., ticket, truck, arrow)
Readability is key – large, bold text and high contrast colors that are visible from a distance
Target Audience:
International truck drivers – people who need fast, clear communication. Not everyone speaks the local language, so visual clarity and multilingual messaging are critical.
File Requirements:
Print-ready file (PDF or EPS) – 300 dpi at 1:10 scale
Include 5 cm bleed on all sides
Provide open source files if possible (AI or PSD)

```html
<!DOCTYPE html>
<html lang="en">
<head>
<meta charset="utf-8">
<title>Haulport 41Ter – Ticket Validation Banner</title>
<link rel="stylesheet" href="https://fonts.googleapis.com/css2?family=Roboto+Condensed:wght@400;500;700;800&display=swap">
<style>
  :root {
    --navy: #20264a;
    --red: #d3202b;
    --blue: #1f7cc4;
    --white: #ffffff;
    --page: #e9ecf1;
  }
  * { box-sizing: border-box; margin: 0; padding: 0; }
  html, body {
    width: 1200px; height: 840px; overflow: hidden;
    background: var(--page);
    font-family: "Roboto Condensed", "Arial Narrow", sans-serif;
  }
  .banner {
    position: absolute; left: 40px; top: 262px;
    width: 1120px; height: 316px;
    background: var(--navy);
    color: var(--white);
  }
  .banner-header {
    position: absolute; left: 0; top: 0; width: 100%; height: 84px;
    border-bottom: 3px solid var(--red);
    display: flex; align-items: center;
    padding-left: 34px;
  }
  .brand {
    display: flex; align-items: center; gap: 8px;
    font-weight: 800; font-size: 26px; line-height: 1;
    color: var(--white); letter-spacing: -0.3px;
    width: 138px;
  }
  .brand-mark {
    width: 14px; height: 14px; background: var(--blue); flex: none;
  }
  .headline {
    margin-left: 14px;
    font-weight: 700; font-size: 29px; letter-spacing: 0.1px;
    white-space: nowrap;
  }
  .must-read {
    position: absolute; left: 30px; top: 98px;
    display: flex; align-items: center; gap: 6px;
    font-weight: 700; font-size: 20px;
  }
  .alert-icon {
    width: 24px; height: 24px; border-radius: 50%;
    border: 2px solid var(--red);
    display: flex; align-items: center; justify-content: center;
    font-size: 16px; font-weight: 800;
  }
  .messages {
    position: absolute; left: 50px; top: 132px;
    list-style: none;
  }
  .message {
    display: flex; align-items: center;
    height: 29px;
    font-weight: 500; font-size: 15.5px; white-space: nowrap;
  }
  .chevrons {
    color: var(--red); font-weight: 700; font-size: 13px;
    width: 26px; letter-spacing: -1px;
  }
  .info-column {
    position: absolute; left: 860px; top: 96px; width: 230px;
    display: flex; flex-direction: column; align-items: center;
  }
  .parking-sign { display: block; }
  .parking-label {
    margin-top: 0;
    background: var(--white); color: #111;
    font-weight: 500; font-size: 22px; letter-spacing: 0.5px;
    padding: 1px 6px; display: flex; align-items: center; gap: 2px;
  }
  .parking-label svg { display: block; }
  .hours-title {
    margin-top: 10px;
    background: var(--blue);
    font-weight: 700; font-size: 19px;
    padding: 1px 6px; border-radius: 3px;
  }
  .hours-row {
    margin-top: 9px;
    font-weight: 700; font-size: 15px; letter-spacing: 0.2px;
    border-bottom: 3px solid var(--red);
    padding: 0 3px 2px;
  }
</style>
</head>
<body>
  <section class="banner">
    <header class="banner-header">
      <div class="brand"><span class="brand-mark"></span>Haulport 41Ter</div>
      <h1 class="headline">"Attention Drivers: Entry Tickets Must Be Verified Inside the Shop."</h1>
    </header>

    <div class="must-read"><span class="alert-icon">!</span>MUST READ!</div>

    <ul class="messages">
      <li class="message"><span class="chevrons">&gt;&gt;</span>English (EN): Don't forget to validate your entry ticket in the shop – mandatory, even for short stops!</li>
      <li class="message"><span class="chevrons">&gt;&gt;</span>French (FR): N'oubliez pas de valider votre ticket à la boutique – obligatoire, même pour un court arrêt !</li>
      <li class="message"><span class="chevrons">&gt;&gt;</span>Dutch (NL): Vergeet je ticket niet te valideren in de shop – verplicht, ook bij kort parkeren!</li>
      <li class="message"><span class="chevrons">&gt;&gt;</span>German (DE): Vergessen Sie nicht, Ihr Einfahrticket im Shop zu entwerten – Pflicht, auch bei kurzem Parken!</li>
      <li class="message"><span class="chevrons">&gt;&gt;</span>Polish (PL): Nie zapomnij zatwierdzić biletu w sklepie – obowiązkowe, nawet przy krótkim postoju!</li>
      <li class="message"><span class="chevrons">&gt;&gt;</span>Romanian (RO): Nu uitați să validați biletul în magazin – obligatoriu, chiar și pentru opriri scurte!</li>
    </ul>

    <aside class="info-column">
      <svg class="parking-sign" width="70" height="90" viewBox="0 0 70 90" aria-label="Parking sign">
        <rect x="31" y="76" width="8" height="14" fill="#ffffff"/>
        <rect x="1.5" y="1.5" width="67" height="76" rx="9" fill="#ffffff"/>
        <rect x="5" y="5" width="60" height="69" rx="7" fill="#1f7cc4"/>
        <text x="35" y="62" text-anchor="middle" font-family="Roboto Condensed, sans-serif" font-weight="700" font-size="58" fill="#ffffff">P</text>
      </svg>
      <div class="parking-label">
        <svg width="22" height="14" viewBox="0 0 22 14"><path d="M21 7H3M8 2L2 7l6 5" stroke="#111" stroke-width="2.2" fill="none"/></svg>
        PARKING
        <svg width="22" height="14" viewBox="0 0 22 14"><path d="M1 7h18M14 2l6 5-6 5" stroke="#111" stroke-width="2.2" fill="none"/></svg>
      </div>
      <div class="hours-title">SHOP OPENING HOURS</div>
      <div class="hours-row">MON – FRI: 05:30 – 22:00</div>
      <div class="hours-row">SAT &amp; SUN: 08:00 – 22:00</div>
    </aside>
  </section>
</body>
</html>
```